Business card for law firm

Need business card for new law firm. Think confident, authoritative, conservative, but not stuffy or old-fashioned.

Contact Information for Business Card

Content for card - logo (uploaded), plus the following:

Paul Whitcombe (larger font)
Managing Partner (larger font, but not as large as name)
Level 9, 7 Ferris Lane
Sydney NSW 2000
Main Tel 02 9364 2710
Direct Tel 02 8472 3159
Email paul@qvlegal.com.au
www.qvlegal.com.au

Letterhead design should include logo plus:
Level 9, 7 Ferris Lane
Sydney NSW 2000
Tel 02 8472 3159
www.qvlegal.com.au

```html
<!DOCTYPE html>
<html lang="en">
<head>
<meta charset="utf-8">
<title>Quayvale Lawyers – Business Card</title>
<link rel="stylesheet" href="https://fonts.googleapis.com/css2?family=Cinzel:wght@400;600&family=Open+Sans:wght@400&display=swap">
<style>
  :root {
    --navy: #0d1f56;
    --ink: #1a1a1a;
    --grey-text: #4a4a4a;
    --panel: #eef0f4;
    --paper: #ffffff;
    --stage: #d9d9d9;
  }
  * { box-sizing: border-box; margin: 0; padding: 0; }
  html, body { width: 1200px; height: 900px; overflow: hidden; }
  body {
    background: var(--stage);
    display: flex;
    align-items: center;
    justify-content: center;
    gap: 60px;
    font-family: "Open Sans", Arial, sans-serif;
  }
  .card {
    width: 520px;
    height: 300px;
    border-radius: 22px;
    position: relative;
    overflow: hidden;
    box-shadow: 0 6px 18px rgba(0,0,0,0.18);
  }

  /* Front (navy) */
  .card--front {
    background: var(--navy);
    display: flex;
    align-items: center;
    justify-content: center;
  }
  .brand {
    display: flex;
    flex-direction: column;
    align-items: center;
    font-family: "Cinzel", Georgia, serif;
    font-weight: 400;
    color: var(--paper);
  }
  .brand__square {
    width: 58px;
    height: 46px;
    background: var(--paper);
    margin-bottom: 10px;
  }
  .brand__name {
    font-size: 44px;
    letter-spacing: 2px;
    line-height: 1;
  }
  .brand__sub {
    font-size: 12px;
    letter-spacing: 17px;
    margin-top: 6px;
    margin-right: -17px;
  }

  /* Back (white) */
  .card--back { background: var(--paper); }
  .card__panel {
    position: absolute;
    top: 0; right: 0;
    width: 180px;
    height: 100%;
    background: var(--panel);
  }
  .card__address {
    position: absolute;
    top: 98px;
    right: 26px;
    text-align: right;
    font-size: 13px;
    line-height: 1.35;
    color: var(--grey-text);
  }
  .card__logo {
    position: absolute;
    top: 46px;
    left: 34px;
    display: flex;
    align-items: flex-end;
    gap: 12px;
    font-family: "Cinzel", Georgia, serif;
    font-weight: 400;
    color: var(--ink);
  }
  .card__logo-square {
    width: 62px;
    height: 48px;
    background: var(--navy);
  }
  .card__logo-text { display: flex; flex-direction: column; }
  .card__logo-name { font-size: 36px; line-height: 1; letter-spacing: 1px; }
  .card__logo-sub { font-size: 10px; letter-spacing: 14px; margin-top: 4px; }

  .contact {
    position: absolute;
    left: 34px;
    top: 138px;
  }
  .contact__name {
    font-family: "Cinzel", Georgia, serif;
    font-weight: 400;
    font-size: 17px;
    color: var(--navy);
    letter-spacing: 0.5px;
    line-height: 1.1;
  }
  .contact__role {
    font-size: 13px;
    color: var(--grey-text);
    margin-bottom: 6px;
  }
  .contact__list { list-style: none; }
  .contact__item {
    display: flex;
    align-items: center;
    gap: 7px;
    font-size: 13px;
    line-height: 1.4;
    color: var(--grey-text);
  }
  .contact__item svg { width: 11px; height: 11px; fill: var(--navy); flex: none; }
  .contact__note { font-size: 10px; }
</style>
</head>
<body>

  <section class="card card--front" aria-label="Card front">
    <div class="brand">
      <div class="brand__square"></div>
      <div class="brand__name">QUAYVALE</div>
      <div class="brand__sub">LAWYERS</div>
    </div>
  </section>

  <section class="card card--back" aria-label="Card back">
    <div class="card__panel"></div>
    <p class="card__address">Level 9, 7 Ferris Lane<br>Sydney NSW 2000</p>

    <div class="card__logo">
      <div class="card__logo-square"></div>
      <div class="card__logo-text">
        <span class="card__logo-name">QUAYVALE</span>
        <span class="card__logo-sub">LAWYERS</span>
      </div>
    </div>

    <div class="contact">
      <h1 class="contact__name">PAUL WHITCOMBE</h1>
      <p class="contact__role">Managing Partner</p>
      <ul class="contact__list">
        <li class="contact__item">
          <svg viewBox="0 0 12 12"><path d="M2 4c0-2 2-3 4-3s4 1 4 3H8L7 3H5L4 4zM3 5h6l1 5H2z"/></svg>
          02 9364 2710
        </li>
        <li class="contact__item">
          <svg viewBox="0 0 12 12"><path d="M2 4c0-2 2-3 4-3s4 1 4 3H8L7 3H5L4 4zM3 5h6l1 5H2z"/></svg>
          02 8472 3159 <span class="contact__note">(DIRECT)</span>
        </li>
        <li class="contact__item">
          <svg viewBox="0 0 12 12"><path d="M1 2h10v8H1z M1 2l5 4 5-4" fill="none" stroke="#0d1f56" stroke-width="1.4"/></svg>
          paul@qvlegal.com.au
        </li>
        <li class="contact__item">
          <svg viewBox="0 0 12 12"><circle cx="6" cy="6" r="5.5"/><path d="M1 6h10M6 1v10" stroke="#fff" stroke-width="0.9"/></svg>
          www.qvlegal.com.au
        </li>
      </ul>
    </div>
  </section>

</body>
</html>
```